DRALVO 2020

I have a front picture for the CD; I have all of the info for the back cover; I need someone to put my idea together with the correct specs; I require a very FAST TURN AROUND!!! I need to get this project to the CD replicator by next week ASAP...

```html
<!DOCTYPE html>
<html lang="en">
<head>
<meta charset="utf-8">
<title>DRALVO 2020 – CD Front and Back</title>
<link rel="stylesheet" href="https://fonts.googleapis.com/css2?family=Montserrat:wght@800;900&family=Poppins:ital,wght@0,500;0,600;1,500&display=swap">
<style>
  :root {
    --stage: #5f5f5f;
    --navy: #14264f;
    --navy-deep: #0d1d3d;
    --navy-light: #2c4679;
    --red: #c8161d;
    --red-deep: #9c0f14;
    --silver: #e9e9ea;
    --silver-dark: #b9bbc0;
    --white: #ffffff;
    --ink: #12203f;
    --flag-blue: #2a3f9a;
    --flag-red: #d8242b;
  }
  * { box-sizing: border-box; margin: 0; padding: 0; }
  html, body { width: 1200px; height: 641px; overflow: hidden; }
  body { background: var(--stage); position: relative; font-family: "Poppins", sans-serif; }

  /* Front cover */
  .front-cover {
    position: absolute; left: 68px; top: 68px; width: 510px; height: 491px;
    overflow: hidden; background: var(--red);
  }
  .front-header {
    position: absolute; left: 0; top: 0; width: 100%; height: 151px;
    background: radial-gradient(ellipse at 50% 100%, var(--navy-light) 0%, var(--navy) 55%, var(--navy-deep) 100%);
    text-align: center;
  }
  .front-title {
    font-family: "Montserrat", sans-serif; font-weight: 900;
    font-size: 104px; line-height: 1; color: var(--silver);
    letter-spacing: -2px; padding-top: 14px;
    text-shadow: 0 3px 4px rgba(0,0,0,.35);
  }
  .front-tagline {
    font-family: "Montserrat", sans-serif; font-weight: 800;
    font-size: 17px; letter-spacing: 4px; color: var(--silver);
    margin-top: 8px;
  }
  .silver-band {
    position: absolute; left: 0; top: 151px; width: 100%; height: 14px;
    background: linear-gradient(to bottom, var(--white), var(--silver-dark));
  }
  .front-art {
    position: absolute; left: 0; top: 165px; width: 100%; height: 315px;
    background: linear-gradient(100deg, var(--flag-blue) 0%, var(--flag-blue) 30%, var(--flag-red) 48%, #f1e6e6 62%, var(--flag-red) 78%, var(--red-deep) 100%);
  }
  .front-year {
    position: absolute; left: 0; top: 160px; width: 100%; text-align: center;
    font-family: "Montserrat", sans-serif; font-weight: 900; font-size: 170px;
    line-height: 1; color: rgba(255,255,255,.82); letter-spacing: -6px;
  }
  .front-frame { position: absolute; left: 0; top: 462px; width: 510px; height: 34px; }
  .front-footer {
    position: absolute; left: 0; top: 491px; width: 100%; height: 100px;
    background: linear-gradient(to bottom, var(--red), var(--red-deep));
  }
  .artist-name {
    position: absolute; left: 0; top: 442px; width: 100%; text-align: center;
    font-family: "Poppins", sans-serif; font-style: italic; font-weight: 500;
    font-size: 15px; letter-spacing: 2px; color: var(--white);
  }

  /* Back cover */
  .back-cover {
    position: absolute; left: 691px; top: 65px; width: 494px; height: 493px;
    overflow: hidden; background: var(--navy-deep);
  }
  .back-header {
    height: 91px; background: var(--navy-deep);
    display: flex; align-items: center; justify-content: center;
  }
  .back-title {
    font-family: "Montserrat", sans-serif; font-weight: 900; font-size: 56px;
    color: var(--white); letter-spacing: -1px; line-height: 1; padding-top: 6px;
  }
  .back-collage {
    position: absolute; left: 0; top: 91px; width: 100%; height: 402px;
    background: linear-gradient(160deg, #d9d4cf 0%, #8a94b4 30%, #2b3f8f 55%, #b6242c 78%, #5a5f8a 100%);
  }
  .track-list { position: absolute; left: 28px; top: 127px; list-style: none; }
  .track {
    height: 16px; margin-bottom: 14.2px; padding-left: 4px;
    font-size: 11.4px; font-weight: 500; line-height: 16px; color: var(--ink);
    background: linear-gradient(to right, var(--white) 70%, rgba(255,255,255,0));
    white-space: nowrap;
  }
</style>
</head>
<body>

  <section class="front-cover">
    <header class="front-header">
      <h1 class="front-title">DRALVO</h1>
      <p class="front-tagline">MUSIC THAT RINGS TRUTH</p>
    </header>
    <div class="silver-band"></div>
    <div class="front-art" role="img" aria-label="Artist photo with arms raised in front of a waving American flag"></div>
    <div class="front-year" aria-hidden="true">2020</div>
    <div class="front-footer"></div>
    <svg class="front-frame" viewBox="0 0 510 34" aria-hidden="true">
      <path d="M0 4 H130 L150 20 H360 L380 4 H510 V12 H384 L364 28 H146 L126 12 H0 Z" fill="var(--silver)"/>
    </svg>
    <p class="artist-name">Nico Varella</p>
  </section>

  <section class="back-cover">
    <header class="back-header">
      <h2 class="back-title">DRALVO 2020</h2>
    </header>
    <div class="back-collage" role="img" aria-label="Collage of rally crowds, campaign signs and stage photos"></div>
    <ol class="track-list">
      <li class="track" style="width:213px">1. DRALVO DERANGEMENT SYNDROME</li>
      <li class="track" style="width:120px">2. WOW THING</li>
      <li class="track" style="width:190px">3. STAR SPANGLED BANNER</li>
      <li class="track" style="width:180px">4. AMERICA IS BEAUTIFUL</li>
      <li class="track" style="width:180px">5. LET DRALVO BE DRALVO</li>
      <li class="track" style="width:160px">6. I BELIEVE IN HIM</li>
      <li class="track" style="width:170px">7. HE'S SO BAD</li>
      <li class="track" style="width:165px">8. NEVER DRALVO BLUES</li>
      <li class="track" style="width:130px">9. PALM HARBOR</li>
    </ol>
  </section>

</body>
</html>
```